Executive Taxi firm with Chauffeur service Website

I have my domain name registered and I have started to work on my site but I am struggling. I am just about to get a logo for the company and need a web site that clearly represents the fact we are an executive/luxury brand in private hire vehicles. We offer airport transfers, train station transfers, seaport transfers, holiday transfers and business to business pick up and drop off.

Target Market(s)

Corporate people, holidaymakers looking for a luxury start their holiday. VIPs' and celebrities.

Number of Pages Required

5+ page

Font styles to use
Serif
Sans Serif
Decorative
Script

Colors

Designer to choose colors to be used in the design.

Requirements
Must have
• Home Page, Services, About Us, VIP and Contact us
• Please see www.brivomotors.co.uk I have started it but not happy with it at all.
Nice to have
• Booking form or enquiry form.

```html
<!DOCTYPE html>
<html lang="en">
<head>
<meta charset="utf-8">
<title>Brivo Motors – Executive Private Hire</title>
<link href="https://fonts.googleapis.com/css2?family=Montserrat:wght@400;600;700;800&family=Open+Sans:wght@400;600;700&display=swap" rel="stylesheet">
<style>
:root{
  --yellow:#f5c400;
  --dark:#141414;
  --tile:#1d1d1d;
  --ink:#222;
  --muted:#777;
  --light:#f2f2f2;
  --white:#fff;
}
*{box-sizing:border-box;margin:0;padding:0}
html,body{width:1200px;height:3332px;overflow:hidden}
body{font-family:"Open Sans",Arial,sans-serif;color:var(--ink);background:var(--white);position:relative}
h1,h2,h3,.btn,.nav a,.brand{font-family:"Montserrat",Arial,sans-serif}
.btn{display:inline-block;background:var(--yellow);color:var(--dark);font-weight:700;font-size:15px;letter-spacing:.5px;padding:14px 34px;border-radius:30px;text-transform:uppercase}

/* header */
.site-header{position:absolute;top:0;left:0;width:1200px;height:88px;background:var(--white);display:flex;align-items:center;padding:0 170px}
.brand{display:flex;align-items:center;gap:12px;font-weight:700;font-size:26px;color:var(--dark)}
.brand-dot{width:30px;height:30px;border-radius:50%;background:var(--yellow)}
.nav{margin-left:auto;display:flex;gap:34px;align-items:center}
.nav a{font-size:14px;font-weight:600;color:var(--dark);text-decoration:none}
.nav .phone{display:flex;align-items:center;gap:8px;border-left:1px solid #ddd;padding-left:26px}

/* hero */
.hero{position:absolute;top:88px;left:0;width:1200px;height:532px;background:linear-gradient(110deg,#5a5048 0%,#2c2a28 40%,#151515 70%,#3a3835 100%);color:var(--white);text-align:center}
.hero-content{position:absolute;top:130px;width:100%}
.hero .kicker{font-family:"Montserrat",sans-serif;font-size:34px;font-weight:400}
.hero h1{font-size:62px;font-weight:800;margin:6px 0 34px}
.hero-arrow{position:absolute;top:240px;width:36px;height:36px;border-radius:50%;border:2px solid rgba(255,255,255,.7);display:flex;align-items:center;justify-content:center}
.hero-arrow.left{left:22px}.hero-arrow.right{right:22px}

/* about */
.about{position:absolute;top:620px;left:0;width:1200px;height:550px}
.about-text{position:absolute;left:170px;top:80px;width:520px}
.about h2{font-size:44px;font-weight:700;color:var(--dark);margin-bottom:30px}
.about p{font-size:14px;line-height:24px;color:#555;margin-bottom:22px}
.about .btn{margin-top:10px}
.about-visual{position:absolute;left:730px;top:60px;width:330px;height:400px;background:linear-gradient(160deg,#eeeae2 0%,#d9d3c6 100%)}

/* services */
.services{position:absolute;top:1170px;left:0;width:1200px;height:630px;background:var(--dark)}
.service-grid{position:absolute;left:170px;top:110px;display:grid;grid-template-columns:repeat(3,280px);gap:30px 22px}
.service{height:230px;background:var(--tile);display:flex;flex-direction:column;align-items:center;justify-content:center;gap:22px;color:var(--white);font-size:16px;text-align:center}
.service.lead{background:var(--yellow);color:var(--dark)}
.service.lead h2{font-size:42px;font-weight:800;line-height:48px}

/* booking */
.booking{position:absolute;top:1800px;left:0;width:1200px;height:680px;background:var(--white)}
.booking h2{position:absolute;top:110px;width:100%;text-align:center;font-size:42px;font-weight:700;color:var(--dark)}
.booking-form{position:absolute;left:250px;top:190px;width:700px;display:grid;grid-template-columns:1fr 1fr;gap:14px 30px}
.field{height:42px;border-bottom:1px solid #ccc;display:flex;align-items:center;justify-content:space-between;font-size:13px;color:#666;padding:0 4px}
.booking .btn{position:absolute;top:378px;left:540px;font-size:12px;padding:10px 22px}
.cityscape{position:absolute;left:0;top:440px;width:1200px;height:240px;background:linear-gradient(#ffffff 0%,#e6e9ee 60%,#b8cbe0 100%)}
.road{position:absolute;left:0;bottom:0;width:1200px;height:46px;background:#a9c3da}

/* news */
.news{position:absolute;top:2480px;left:0;width:1200px;height:540px;background:var(--light)}
.news h2{position:absolute;top:60px;width:100%;text-align:center;font-size:42px;font-weight:700;color:var(--dark)}
.news-grid{position:absolute;left:170px;top:150px;display:grid;grid-template-columns:repeat(3,270px);gap:0 45px}
.news-card{background:var(--white);height:330px;position:relative}
.news-date{position:absolute;top:-4px;left:0;background:var(--yellow);font-family:"Montserrat",sans-serif;font-weight:700;font-size:13px;padding:6px 12px}
.news-photo{position:absolute;top:28px;left:14px;right:14px;height:150px}
.news-card h3{position:absolute;top:196px;left:14px;right:14px;font-size:14px;font-weight:700;line-height:20px}
.news-card p{position:absolute;top:246px;left:14px;right:14px;font-size:12px;line-height:19px;color:var(--muted)}

/* footer */
.site-footer{position:absolute;top:3020px;left:0;width:1200px;height:312px;background:var(--dark);border-top:6px solid var(--yellow);color:var(--white)}
.footer-cols{position:absolute;left:170px;top:30px;display:flex;gap:0}
.footer-col{width:150px}
.footer-col h3{font-size:17px;font-weight:700;margin-bottom:16px}
.footer-col li{list-style:none;font-size:12px;color:#aaa;line-height:21px}
.newsletter{position:absolute;left:720px;top:30px;width:310px}
.newsletter h3{font-size:17px;font-weight:700;margin-bottom:16px}
.signup{display:flex;height:34px}
.signup span{flex:1;background:var(--white);color:#999;font-size:12px;display:flex;align-items:center;padding-left:10px}
.signup b{background:var(--yellow);color:var(--dark);font-family:"Montserrat",sans-serif;font-size:12px;display:flex;align-items:center;padding:0 16px}
.follow{margin-top:22px;display:flex;align-items:center;gap:10px;color:var(--yellow);font-family:"Montserrat",sans-serif;font-weight:700;font-size:16px}
.follow i{width:22px;height:22px;border-radius:50%;background:var(--yellow);display:inline-block}
.footer-bar{position:absolute;left:170px;right:170px;bottom:0;height:70px;border-top:1px solid #333;display:flex;align-items:center;gap:40px;font-size:12px;color:#aaa}
.footer-bar .brand{color:var(--white);font-size:22px}
.footer-bar .brand-dot{width:24px;height:24px}
.footer-bar .copy{margin-left:auto}
</style>
</head>
<body>

<header class="site-header">
  <div class="brand"><span class="brand-dot"></span>Brivo Motors</div>
  <nav class="nav">
    <a>Home</a><a>Services</a><a>About Us</a><a>VIP</a><a>Contact Us</a>
    <a class="phone"><svg width="14" height="14" viewBox="0 0 24 24"><path fill="#141414" d="M6.6 10.8a15 15 0 0 0 6.6 6.6l2.2-2.2a1 1 0 0 1 1-.25 11.4 11.4 0 0 0 3.6.57 1 1 0 0 1 1 1V20a1 1 0 0 1-1 1A17 17 0 0 1 3 4a1 1 0 0 1 1-1h3.5a1 1 0 0 1 1 1c0 1.25.2 2.45.57 3.57a1 1 0 0 1-.25 1z"/></svg>01632 960 184</a>
  </nav>
</header>

<section class="hero" role="img" aria-label="Photo of a smiling businesswoman stepping out of a dark executive car">
  <div class="hero-content">
    <p class="kicker">Private Hire, Chauffeur and taxi service</p>
    <h1>Executive Brivo Motors</h1>
    <span class="btn">Book Now</span>
  </div>
  <span class="hero-arrow left"><svg width="12" height="12" viewBox="0 0 12 12"><path d="M8 1 3 6l5 5" stroke="#fff" stroke-width="2" fill="none"/></svg></span>
  <span class="hero-arrow right"><svg width="12" height="12" viewBox="0 0 12 12"><path d="M4 1l5 5-5 5" stroke="#fff" stroke-width="2" fill="none"/></svg></span>
</section>

<section class="about">
  <div class="about-text">
    <h2>Always here for you</h2>
    <p>We provide airport transfers to and from all major UK airports, seaports and train stations in comfort, with executive vehicles and professional chauffeurs. Whether you travel as an individual, a family or a corporate group, our team offers a reliable, discreet and punctual service tailored to your needs.</p>
    <p>We aim to make every journey calm and effortless. Our drivers track your flight or train, meet you on arrival and help with luggage, so you can relax from the moment you step inside. Book online and let us take care of the rest.</p>
    <span class="btn">Hire Vehicles</span>
  </div>
  <div class="about-visual" role="img" aria-label="Illustration of a smartphone with a taxi booking app over a circular city map"></div>
</section>

<section class="services">
  <div class="service-grid">
    <div class="service lead"><h2>Our<br>Services</h2></div>
    <div class="service">
      <svg width="54" height="54" viewBox="0 0 24 24"><path fill="#fff" d="M21 16v-2l-8-5V3.5a1.5 1.5 0 0 0-3 0V9l-8 5v2l8-2.5V19l-2 1.5V22l3.5-1 3.5 1v-1.5L13 19v-5.5z"/></svg>
      Airport Transfers</div>
    <div class="service">
      <svg width="54" height="54" viewBox="0 0 24 24" fill="none" stroke="#fff" stroke-width="1.6"><rect x="5" y="3" width="14" height="14" rx="3"/><path d="M5 10h14M8 21l2-4M16 21l-2-4"/><circle cx="9" cy="13.5" r="1" fill="#fff"/><circle cx="15" cy="13.5" r="1" fill="#fff"/></svg>
      Train Station Transfers</div>
    <div class="service">
      <svg width="54" height="54" viewBox="0 0 24 24" fill="none" stroke="#fff" stroke-width="1.6"><path d="M3 15h18l-3 5H6zM6 15V9h12v6M10 9V5h4v4"/></svg>
      Seaport Transfers</div>
    <div class="service">
      <svg width="54" height="54" viewBox="0 0 24 24" fill="none" stroke="#fff" stroke-width="1.6"><path d="M3 11a9 9 0 0 1 18 0zM12 11v8a2 2 0 0 1-4 0"/><path d="M2 21h20"/></svg>
      Holiday Transfers</div>
    <div class="service">
      <svg width="54" height="54" viewBox="0 0 24 24" fill="none" stroke="#fff" stroke-width="1.6"><rect x="3" y="11" width="18" height="7" rx="2"/><path d="M6 11l2-5h8l2 5M10 6V4h4v2"/><circle cx="7" cy="18.5" r="1.5"/><circle cx="17" cy="18.5" r="1.5"/></svg>
      Business to Business<br>Pick up &amp; drop off</div>
  </div>
</section>

<section class="booking">
  <svg style="position:absolute;left:575px;top:50px" width="50" height="40" viewBox="0 0 50 40"><path d="M2 20 48 2 36 38 24 26z" fill="#ddd"/><path d="M24 26 48 2 20 30z" fill="#bbb"/></svg>
  <h2>Book a Ride with Us</h2>
  <div class="booking-form">
    <div class="field">First Name</div><div class="field">Phone</div>
    <div class="field">Last Name</div><div class="field">Date<svg width="14" height="14" viewBox="0 0 14 14"><rect x="1" y="2" width="12" height="11" fill="none" stroke="#888"/><path d="M1 5h12" stroke="#888"/></svg></div>
    <div class="field">Email</div><div class="field">Time<svg width="14" height="14" viewBox="0 0 14 14"><circle cx="7" cy="7" r="6" fill="none" stroke="#888"/><path d="M7 3v4h3" stroke="#888" fill="none"/></svg></div>
  </div>
  <span class="btn">Submit Now</span>
  <div class="cityscape" role="img" aria-label="Illustration of a city skyline with two yellow taxis on the road">
    <div class="road"></div>
  </div>
</section>

<section class="news">
  <h2>Latest News</h2>
  <div class="news-grid">
    <article class="news-card">
      <div class="news-photo" role="img" aria-label="Photo of a yellow taxi on a city street" style="background:linear-gradient(135deg,#e9c23a,#6b6152)"></div>
      <span class="news-date">Oct 31 2016</span>
      <h3>SED UT PERSPICIATIS UNDE OMNIS ISTEUS</h3>
      <p>Our chauffeurs share travel tips for a calm and easy start to your holiday.</p>
    </article>
    <article class="news-card">
      <div class="news-photo" role="img" aria-label="Photo of a passenger using a phone in the back of a car" style="background:linear-gradient(135deg,#c9b9a3,#3f3a35)"></div>
      <span class="news-date">Oct 31 2016</span>
      <h3>SED UT PERSPICIATIS UNDE OMNIS ISTEUS</h3>
      <p>Our chauffeurs share travel tips for a calm and easy start to your holiday.</p>
    </article>
    <article class="news-card">
      <div class="news-photo" role="img" aria-label="Photo of yellow taxis lined up at a station" style="background:linear-gradient(135deg,#f0c82e,#8a7a50)"></div>
      <span class="news-date">Oct 31 2016</span>
      <h3>SED UT PERSPICIATIS UNDE OMNIS ISTEUS</h3>
      <p>Our chauffeurs share travel tips for a calm and easy start to your holiday.</p>
    </article>
  </div>
</section>

<footer class="site-footer">
  <div class="footer-cols">
    <div class="footer-col"><h3>Support</h3><ul><li>Help centre</li><li>Booking help</li><li>Cancellations</li><li>Lost property</li><li>Contact us</li></ul></div>
    <div class="footer-col"><h3>Company</h3><ul><li>About us</li><li>Our fleet</li><li>Careers</li><li>Press</li><li>Partners</li></ul></div>
    <div class="footer-col"><h3>Links</h3><ul><li>Airport transfers</li><li>Holiday transfers</li><li>Seaport transfers</li><li>VIP service</li><li>Business travel</li></ul></div>
  </div>
  <div class="newsletter">
    <h3>Newsletter</h3>
    <div class="signup"><span>Email</span><b>SIGN UP</b></div>
    <div class="follow">Follow us on <i></i><i></i><i></i></div>
  </div>
  <div class="footer-bar">
    <div class="brand"><span class="brand-dot"></span>Brivo Motors</div>
    <span>01632 960 184</span>
    <span>info@brivomotors.co.uk</span>
    <span class="copy">© 2016 All Rights Are Reserved Terms of Use | Privacy Policy</span>
  </div>
</footer>

</body>
</html>
```